Brightline Energy Product Distribution Brochure

We are looking to have our current brochure for our customers completely redesigned...the idea is to present the relevant information in an attractive way . Our website is brightlineenergyco.example where you can find more information about us. We have included a file with a rough idea of the page order and what each should include but feel free to adapt based on design. The example provided is only for context and doesnt have to be maintained. We will be using the brochure both digitally and in print form. As long as it reads easily and is eye catching, the design can be horizontal or vertical.Final deliverable should be indesign file.

"Our Brands" page: should be limited to one page (space being enough) where it has the header for each one (for example diesel generators) space for one or two lines of text and then the corresponding logos for each of the five categories
Updates

For those asking: the "our brands" page should be a single page layout where there is a header with the corresponding section and space for maybe one line of text followed by the two logos for that category. Each of the product pages should be similar in fashion to the one in the document attached: a photo of the product with some white space and space for the text to be included. We will be posting additional examples today

Target Market(s)

We want to present it to customers both digitally and in print so they can see our products

Industry/Entity Type

Power Generation

Font styles to use
Serif

Requirements
Must have
• Eye catching and able to present the information in a presentable fashion. Rest is up to you.
Nice to have
• Should incorporate the colors of our logo but can also add other depending on design

```html
<!DOCTYPE html>
<html lang="en">
<head>
<meta charset="utf-8">
<title>Brightline Energy – Product Brochure Spread</title>
<link href="https://fonts.googleapis.com/css2?family=Archivo+Black&family=Montserrat:wght@500;600&family=Work+Sans:wght@400&display=swap" rel="stylesheet">
<style>
  :root{
    --stage-light:#d1d2d4;
    --stage-dark:#7c7d81;
    --navy:#0e3456;
    --yellow:#f7b714;
    --yellow-soft:#ffd84a;
    --slate:#4a4a4d;
    --white:#ffffff;
    --ink:#1d1d1f;
  }
  *{margin:0;padding:0;box-sizing:border-box}
  html,body{width:1200px;height:801px;overflow:hidden;background:var(--stage-light)}
  .stage{position:relative;width:1200px;height:801px;overflow:hidden}
  .stage-band{position:absolute;inset:0}
  .spread{position:absolute;left:86px;top:71px;width:1030px;height:669px;overflow:hidden;background:var(--navy)}
  .spread-art{position:absolute;inset:0}
  .photo{position:absolute}
  .kicker{position:absolute;font-family:"Montserrat",sans-serif;font-weight:600;font-size:23px;color:var(--white);letter-spacing:.5px;line-height:1}
  .kicker::after{content:"";position:absolute;left:0;top:30px;width:47px;height:3px;background:var(--yellow)}
  .title{position:absolute;font-family:"Archivo Black",sans-serif;font-size:35px;line-height:1;color:var(--yellow);letter-spacing:-.5px;white-space:nowrap;font-weight:400}
  .subtitle{position:absolute;font-family:"Montserrat",sans-serif;font-weight:500;font-size:20px;line-height:24px;color:var(--white)}
  .label{position:absolute;font-family:"Montserrat",sans-serif;font-weight:500;font-size:14px;color:var(--yellow);letter-spacing:.3px}
  .panel{position:absolute;background:var(--white)}
  .features{position:absolute;left:39px;top:23px;width:252px;list-style:none;font-family:"Work Sans",sans-serif;font-size:8.6px;line-height:11.2px;color:var(--ink)}
  .features li{position:relative;padding-left:13px}
  .features li::before{content:"";position:absolute;left:0;top:3px;width:4px;height:4px;border-radius:50%;background:var(--yellow)}
  .copy{position:absolute;font-family:"Work Sans",sans-serif;font-size:8.6px;line-height:11.2px;color:var(--ink)}
  .page-tab{position:absolute;top:640px;height:29px;width:84px;background:var(--yellow);clip-path:polygon(14% 0,100% 0,86% 100%,0 100%)}
  .page-num{position:absolute;top:641px;font-family:"Archivo Black",sans-serif;font-size:22px;line-height:28px;color:var(--ink)}
</style>
</head>
<body>
<div class="stage">
  <svg class="stage-band" width="1200" height="801" aria-hidden="true">
    <polygon points="0,606 1200,314 1200,801 0,801" fill="var(--stage-dark)"/>
  </svg>

  <section class="spread">
    <svg class="spread-art" width="1030" height="669" aria-hidden="true">
      <defs>
        <linearGradient id="sunset" x1="0" y1="0" x2="0" y2="1">
          <stop offset="0" stop-color="#3b4250"/>
          <stop offset=".35" stop-color="#8a5a33"/>
          <stop offset=".6" stop-color="#4a3a36"/>
          <stop offset="1" stop-color="#2b2f3a"/>
        </linearGradient>
        <linearGradient id="refinery-gold" x1="0" y1="0" x2="1" y2="1">
          <stop offset="0" stop-color="#c8a12a"/>
          <stop offset=".5" stop-color="#f1c83a"/>
          <stop offset="1" stop-color="#b48a24"/>
        </linearGradient>
        <linearGradient id="night-plant" x1="0" y1="0" x2="1" y2="0">
          <stop offset="0" stop-color="#0d3a63"/>
          <stop offset=".6" stop-color="#1f4c72"/>
          <stop offset="1" stop-color="#3a5f80"/>
        </linearGradient>
        <linearGradient id="plant-lights" x1="0" y1="0" x2="1" y2="0">
          <stop offset="0" stop-color="#d9a63a"/>
          <stop offset=".45" stop-color="#6b7f95"/>
          <stop offset="1" stop-color="#9fb3c6"/>
        </linearGradient>
      </defs>
      <g role="img" aria-label="Industrial skyline with smokestacks at sunset">
        <rect x="0" y="0" width="517" height="669" fill="url(#sunset)"/>
      </g>
      <g role="img" aria-label="Refinery at night glowing in yellow light">
        <polygon points="0,580 517,330 517,669 0,669" fill="url(#refinery-gold)"/>
      </g>
      <g role="img" aria-label="Power plant towers under a dark blue sky">
        <rect x="517" y="0" width="513" height="669" fill="url(#night-plant)"/>
      </g>
      <polygon points="750,233 1030,60 1030,233" fill="var(--yellow-soft)"/>
      <g role="img" aria-label="Industrial plant piping lit at dusk">
        <rect x="517" y="464" width="513" height="205" fill="url(#plant-lights)"/>
      </g>
      <polyline points="340,690 690,470 790,530" fill="none" stroke="var(--yellow)" stroke-width="12"/>
      <polyline points="470,690 780,478 1040,615" fill="none" stroke="var(--slate)" stroke-width="12"/>
      <polyline points="970,600 1040,650" fill="none" stroke="var(--yellow)" stroke-width="10"/>
    </svg>

    <!-- Left page: diesel generators -->
    <div class="kicker" style="left:36px;top:50px">OUR PRODUCT</div>
    <h1 class="title" style="left:36px;top:92px">DIESEL GENERATORS</h1>
    <div class="subtitle" style="left:36px;top:148px">RENTAL<br>GENERATORS</div>
    <div class="photo" role="img" aria-label="White enclosed 100 kW diesel generator with Brightline Energy branding" style="left:194px;top:145px;width:273px;height:176px;background:linear-gradient(180deg,#f4f4f4 0%,#e2e2e2 85%,#222 86%,#222 100%)"></div>
    <div class="label" style="left:38px;top:269px">FEATURES</div>

    <div class="panel" style="left:0;top:297px;width:347px;height:278px">
      <ul class="features">
        <li>30 to 500 KW powered by Ridgefield diesel engines. EPA Tier 2, Tier 3 and Tier i4</li>
        <li>13 to 60 KW powered by Vantor diesel engines. EPA Tier i4</li>
        <li>Lemaire Voss alternators • Ashcombe (Corvan Generator Technologies) alternators [optional]</li>
        <li>Tidewell TW-70 series controllers for stand-alone operation • Tidewell TW-80 series controllers for paralleling operation [optional]</li>
        <li>12-Gauge steel enclosures with stainless steel hardware</li>
        <li>12-Gauge 5052 aluminum enclosures with stainless steel hardware [optional]</li>
        <li>Quietek Hushline QX critical grade silencers</li>
        <li>Dalmora manual main line circuit breakers</li>
        <li>Norvik manual and motorized main line circuit breakers [optional]</li>
        <li>50 to 5000-Gal, single-wall fuel tanks</li>
        <li>50 to 5000-Gal, double-walled UL142 listed fuel tanks</li>
        <li>Battery disconnect switch</li>
        <li>12V starting battery</li>
      </ul>
    </div>

    <div class="photo" role="img" aria-label="Close view of refinery pipework at sunset" style="left:359px;top:362px;width:116px;height:116px;background:linear-gradient(135deg,#6f87a6,#d98a3c 60%,#f0b04a)"></div>
    <div class="photo" role="img" aria-label="Engine room with orange machinery" style="left:359px;top:485px;width:116px;height:116px;background:linear-gradient(135deg,#9fb8d4,#c9d4df 50%,#e0762b)"></div>

    <div class="page-tab" style="left:0"></div>
    <div class="page-num" style="left:28px">08</div>

    <!-- Right page: AC alternators -->
    <div class="kicker" style="left:550px;top:50px">OUR PRODUCT</div>
    <h2 class="title" style="left:550px;top:92px">AC ALTERNATORS</h2>
    <div class="label" style="left:550px;top:199px">DESCRIPTION</div>

    <div class="panel" style="left:549px;top:231px;width:481px;height:233px"></div>
    <p class="copy" style="left:571px;top:255px;width:172px">Lorem ipsum dolor sit amet, consectetuer adipiscing elit, sed diam nonummy nibh euismod tincidunt ut laoreet dolore magna aliquam erat volutpat. Ut wisi enim ad minim veniam, quis nostrud exerci tation ullamcorper suscipit lobortis nisl ut aliquip ex ea commodo consequat. Duis autem vel eum iriure dolor in hendrerit in vulputate velit esse molestie consequat, vel illum dolore eu feugiat nulla facilisis at vero eros et accumsan et iusto odio dignissim qui blandit praesent luptatum zzril delenit augue duis dolore te feugait nulla facilisi.</p>
    <p class="copy" style="left:779px;top:350px;width:224px">Lorem ipsum dolor sit amet, consectetuer adipiscing elit, sed diam nonummy nibh euismod tincidunt ut laoreet dolore magna aliquam erat volutpat. Ut wisi enim ad minim veniam, quis nostrud exerci tation ullamcorper suscipit lobortis nisl ut aliquip ex ea commodo consequat. Duis autem vel eum iriure dolor in hendrerit in vulputate velit esse molestie consequat.</p>
    <div class="photo" role="img" aria-label="Black brushless AC alternator" style="left:782px;top:140px;width:236px;height:186px;border-radius:40% 10% 10% 40%;background:radial-gradient(circle at 30% 55%,#4a4a4c,#111 70%)"></div>

    <div class="photo" role="img" aria-label="Refinery pipework at sunset" style="left:739px;top:509px;width:115px;height:115px;background:linear-gradient(135deg,#6f87a6,#d98a3c 60%,#f0b04a)"></div>
    <div class="photo" role="img" aria-label="Engine room with orange machinery" style="left:864px;top:509px;width:115px;height:115px;background:linear-gradient(135deg,#9fb8d4,#c9d4df 50%,#e0762b)"></div>

    <div class="page-tab" style="left:515px"></div>
    <div class="page-num" style="left:543px">09</div>
  </section>
</div>
</body>
</html>
```